Business Card Design for Varomir Facility Services

We are looking for a Business Card Design for the Company "Varomir Facility Services."
Front side:
- Company Logo (small)
- Company Name, address, pohone, website and personal data.
- white background, for text e.g. company colors (blue or green like in the logo)
Please use following data:
Company data:
Varomir Facility Services Kostelac
Birkenhaldweg 14
6330 Cham
www.varomir-fs.ch
Person data:
Tarik Kostelac
Geschäftsführer
+41 76 519 47 83
info@varomir-fs.ch
Back side:
could be colored in blue or green
please use a big logo sing and some smaller icons to say what is all beeing offered in facility services, like cleaning, maintenance cleaning
industrial cleaning, caretaking, gardening, disposal. There is no need for everyone of the icons if there are similar or an icon is standing for more of them.
colors to use:
blue: HEX 246BB0
green: HEX 52B33E

```html
<!DOCTYPE html>
<html lang="de">
<head>
<meta charset="utf-8">
<title>Varomir Facility Services – Visitenkarte</title>
<link rel="stylesheet" href="https://fonts.googleapis.com/css2?family=Source+Sans+3:wght@400;600&display=swap">
<style>
  :root {
    --brand-blue: #246bb0;
    --card-blue: #3373b4;
    --brand-green: #52b33e;
    --ink: #3b3b3b;
    --paper: #ffffff;
    --page: #ffffff;
  }
  * { box-sizing: border-box; margin: 0; padding: 0; }
  html, body {
    width: 1200px; height: 960px; overflow: hidden;
    background: var(--page);
    font-family: "Source Sans 3", "Source Sans Pro", sans-serif;
  }
  .canvas { position: relative; width: 1200px; height: 960px; }

  .card {
    position: absolute; left: 286px; width: 629px; height: 359px;
    box-shadow: 0 2px 6px rgba(0,0,0,.35);
  }
  .card--front { top: 109px; background: var(--paper); }
  .card--back { top: 492px; background: var(--card-blue); color: var(--paper); }

  /* front */
  .front__brand {
    position: absolute; left: 20px; top: 181px; transform: translateY(-50%);
    display: flex; align-items: center; gap: 10px;
    color: var(--brand-blue); font-weight: 600; font-size: 21px; letter-spacing: .5px;
  }
  .front__brand-mark { width: 16px; height: 16px; background: var(--brand-green); }
  .front__person { position: absolute; right: 46px; top: 65px; text-align: right; }
  .front__name { font-size: 24px; font-weight: 600; color: var(--ink); line-height: 28px; }
  .front__role { font-size: 19px; color: var(--brand-blue); line-height: 28px; }
  .front__accent {
    position: absolute; right: 0; top: 67px; width: 23px; height: 45px; background: var(--brand-blue);
  }
  .contact-list { position: absolute; right: 44px; top: 217px; list-style: none; }
  .contact-list li {
    display: flex; justify-content: flex-end; align-items: center; gap: 12px;
    height: 26.3px; font-size: 16.5px; color: var(--ink);
  }
  .contact-list svg { width: 16px; height: 16px; fill: var(--brand-blue); flex: none; }

  /* back */
  .back__mark {
    position: absolute; left: 280px; top: 113px; width: 68px; height: 68px;
    border-radius: 50%; background: var(--paper);
  }
  .back__brand {
    position: absolute; left: 0; right: 0; top: 196px; text-align: center;
    font-size: 32px; font-weight: 600; letter-spacing: 1px;
  }
  .services { position: absolute; top: 277px; left: 0; right: 0; list-style: none; }
  .services li {
    position: absolute; display: flex; align-items: center; gap: 10px;
    font-size: 17.5px; white-space: nowrap;
  }
  .services svg { width: 14px; height: 14px; fill: var(--paper); }
</style>
</head>
<body>
<main class="canvas">

  <section class="card card--front" aria-label="Vorderseite">
    <div class="front__brand"><span class="front__brand-mark"></span>Varomir Facility Services</div>
    <div class="front__person">
      <p class="front__name">Tarik Kostelac</p>
      <p class="front__role">Geschäftsführer</p>
    </div>
    <div class="front__accent"></div>
    <ul class="contact-list">
      <li>+41 76 519 47 83
        <svg viewBox="0 0 24 24"><path d="M6.6 10.8a15 15 0 0 0 6.6 6.6l2.2-2.2c.3-.3.7-.4 1-.2 1.1.4 2.3.6 3.6.6.6 0 1 .4 1 1V20c0 .6-.4 1-1 1A17 17 0 0 1 3 4c0-.6.4-1 1-1h3.5c.6 0 1 .4 1 1 0 1.3.2 2.5.6 3.6.1.3 0 .7-.2 1z"/></svg></li>
      <li>info@varomir-fs.ch
        <svg viewBox="0 0 24 24"><path d="M2 5h20v14H2z M3.5 6.5 12 13l8.5-6.5" fill="none" stroke="#246bb0" stroke-width="0"/><path d="M2 5h20v14H2zm2 2v.3l8 6 8-6V7zm0 2.8V17h16V9.8l-8 6z"/></svg></li>
      <li>www.varomir-fs.ch
        <svg viewBox="0 0 24 24"><path d="M12 2a10 10 0 1 0 0 20 10 10 0 0 0 0-20zm0 2c1.2 0 2.4 2.6 2.8 6H9.2C9.6 6.6 10.8 4 12 4zm-5 6H4.3A8 8 0 0 1 8.6 4.8 13 13 0 0 0 7 10zm0 4a13 13 0 0 0 1.6 5.2A8 8 0 0 1 4.3 14zm2.2 0h5.6c-.4 3.4-1.6 6-2.8 6s-2.4-2.6-2.8-6zM17 14h2.7a8 8 0 0 1-4.3 5.2A13 13 0 0 0 17 14zm0-4a13 13 0 0 0-1.6-5.2 8 8 0 0 1 4.3 5.2z"/></svg></li>
      <li>Birkenhaldweg 14, 6330 Cham
        <svg viewBox="0 0 24 24"><path d="M12 1a6 6 0 0 0-6 6c0 4.5 6 10 6 10s6-5.5 6-10a6 6 0 0 0-6-6zm0 8.3A2.3 2.3 0 1 1 12 4.7a2.3 2.3 0 0 1 0 4.6zM4 20c0-1.5 2.5-2.6 5.5-3l.8 1.2C7.8 18.5 6 19.2 6 20s2.7 1.5 6 1.5 6-.7 6-1.5-1.8-1.5-4.3-1.8l.8-1.2c3 .4 5.5 1.5 5.5 3 0 1.9-3.6 3-8 3s-8-1.1-8-3z"/></svg></li>
    </ul>
  </section>

  <section class="card card--back" aria-label="Rückseite">
    <div class="back__mark"></div>
    <p class="back__brand">Varomir Facility Services</p>
    <ul class="services">
      <li style="left:40px;top:0"><svg viewBox="0 0 24 24"><path d="M12 0 14 10 24 12 14 14 12 24 10 14 0 12 10 10z"/></svg>Like cleaning</li>
      <li style="left:40px;top:26px"><svg viewBox="0 0 24 24"><path d="M12 0 14 10 24 12 14 14 12 24 10 14 0 12 10 10z"/></svg>Maintenance cleaning</li>
      <li style="left:273px;top:0"><svg viewBox="0 0 24 24"><path d="M12 0 14 10 24 12 14 14 12 24 10 14 0 12 10 10z"/></svg>Industrial cleaning</li>
      <li style="left:273px;top:26px"><svg viewBox="0 0 24 24"><path d="M12 0 14 10 24 12 14 14 12 24 10 14 0 12 10 10z"/></svg>Caretaking</li>
      <li style="left:485px;top:0"><svg viewBox="0 0 24 24"><path d="M12 0 14 10 24 12 14 14 12 24 10 14 0 12 10 10z"/></svg>Gardening</li>
      <li style="left:485px;top:26px"><svg viewBox="0 0 24 24"><path d="M12 0 14 10 24 12 14 14 12 24 10 14 0 12 10 10z"/></svg>Disposal</li>
    </ul>
  </section>

</main>
</body>
</html>
```